New bussiness card, using company logo.
Lionel Brisk
Manager/Director
Brisk Property Developments
Po Box 5347
Thuringowa Central
Qld
0491 638 205
lionel@briskpropertydevelopments
eye catching, vibrant colours, professional

```html
<!DOCTYPE html>
<html lang="en">
<head>
<meta charset="utf-8">
<title>Brisk Property Developments – Business Card</title>
<link rel="stylesheet" href="https://fonts.googleapis.com/css2?family=Open+Sans:wght@400;600;700&display=swap">
<style>
  :root {
    --backdrop: #3b3531;
    --card: #ffffff;
    --brand-red: #d8262c;
    --brand-green: #7cc242;
    --text-dark: #1f1f1f;
    --text-grey: #6b6b6b;
  }
  * { margin: 0; padding: 0; box-sizing: border-box; }
  html, body {
    width: 1200px; height: 382px; overflow: hidden;
    background: var(--backdrop);
    font-family: "Open Sans", Arial, sans-serif;
  }
  .canvas { position: relative; width: 1200px; height: 382px; }
  .card {
    position: absolute; top: 30px; width: 568px; height: 322px;
    background: var(--card); border-radius: 24px; overflow: hidden;
  }
  .card--front { left: 27px; }
  .card--back { left: 613px; }

  .brand-name {
    position: absolute; display: flex; align-items: center; gap: 8px;
    color: var(--brand-red); font-weight: 700; letter-spacing: -0.2px;
  }
  .brand-name__mark { width: 14px; height: 14px; background: var(--brand-green); flex: none; }
  .card--front .brand-name { left: 40px; top: 70px; font-size: 21px; }
  .card--back .brand-name { left: 0; right: 0; top: 212px; justify-content: center; font-size: 24px; }

  .person { position: absolute; left: 40px; top: 140px; }
  .person__name { color: var(--brand-red); font-weight: 700; font-size: 17px; line-height: 22px; }
  .person__role { color: var(--text-grey); font-size: 13px; line-height: 18px; }

  .contact { position: absolute; left: 40px; top: 208px; list-style: none; }
  .contact__item {
    display: flex; align-items: center; gap: 7px;
    font-size: 14px; line-height: 22px; color: var(--text-dark);
  }
  .contact__icon { width: 12px; height: 12px; fill: var(--brand-green); flex: none; }

  .address { position: absolute; left: 40px; top: 275px; font-size: 14px; color: var(--text-dark); }

  .services {
    position: absolute; left: 0; right: 0; top: 264px;
    display: flex; justify-content: center; gap: 12px;
    list-style: none; font-size: 18px; color: var(--text-dark);
  }
  .services__item { display: flex; align-items: center; gap: 5px; }
  .services__item::before {
    content: ""; width: 7px; height: 7px; border-radius: 50%; background: var(--brand-green);
  }
  .website {
    position: absolute; left: 0; right: 0; top: 291px; text-align: center;
    font-size: 14px; letter-spacing: 0.6px; color: var(--text-dark);
  }
  .website__domain { color: var(--brand-red); font-weight: 700; }
</style>
</head>
<body>
<main class="canvas">
  <section class="card card--front">
    <div class="brand-name"><span class="brand-name__mark"></span>Brisk Property Developments</div>
    <div class="person">
      <p class="person__name">Lionel Brisk</p>
      <p class="person__role">Manager/Director</p>
    </div>
    <ul class="contact">
      <li class="contact__item">
        <svg class="contact__icon" viewBox="0 0 12 12" aria-hidden="true"><path d="M2.5 0.8 4.3 3c.3.4.2.8-.1 1.1l-.8.7c.6 1.3 1.7 2.4 3 3l.7-.8c.3-.3.7-.4 1.1-.1l2.2 1.8c.3.3.3.7 0 1l-1 1c-.6.6-1.5.7-2.3.4C4.4 9.2 2.8 7.6 1 4.9.7 4.1.8 3.2 1.4 2.6l1-1c.3-.3.7-.3.1-.8z"/></svg>
        0491 638 205
      </li>
      <li class="contact__item">
        <svg class="contact__icon" viewBox="0 0 12 12" aria-hidden="true"><path d="M0 3.5 6 0l6 3.5V11H0z M1.2 4.2 6 7.4l4.8-3.2L6 1.4z"/></svg>
        lionel@briskpropertydevelopments.com
      </li>
    </ul>
    <p class="address">Po Box 5347, Thuringowa Central , Qld</p>
  </section>

  <section class="card card--back">
    <div class="brand-name"><span class="brand-name__mark"></span>Brisk Property Developments</div>
    <ul class="services">
      <li class="services__item">Demolish</li>
      <li class="services__item">Renovate</li>
      <li class="services__item">New Constructions</li>
    </ul>
    <p class="website">www.<span class="website__domain">briskpropertydevelopments</span>.com</p>
  </section>
</main>
</body>
</html>
```